Non fiction leadership Book Cover design needed for “Stay Bold: Build On Lasting Discipline”

I need a front cover design for a new book 6 X 9 traditional non-fiction book.

Title: "Stay BOLD - Build On Lasting Discipline"

The subtitle is not finalized- so use 2 lines of smaller dummy text

My brand guide is attached (please use the tan color sparingly)

I'd like to see BOLD look like it is in motion and "flying" across the page

Need CREATIVE designs and options

Do not want my picture on the front cover - I do want it on the back cover.

On the front cover I’d like to see creative use of font to create movement on “BOLD”

Target Market(s)

Business leaders

Industry/Entity Type

Aviation

Font styles to use
Other font styles liked:
• See style guide- can add additional font (modern script or san serif)

Colors
0054AA
0677BA
7BADD7
CADEEF
E8F1F8
EB3D1F
EC4F4E
F09395
F8D3D4
FCEDEE

Requirements
Must have
• Creative font use, using perspective to create movement/motion on BOLD
Should not have
• My picture on the front cover- my picture should be on the back cover

```html
<!DOCTYPE html>
<html lang="en">
<head>
<meta charset="UTF-8">
<title>Stay Bold: Build On Lasting Discipline — Front Cover</title>
<link href="https://fonts.googleapis.com/css2?family=Bebas+Neue&family=Kaushan+Script&family=Montserrat:wght@500;700;800&display=swap" rel="stylesheet">
<style>
  :root {
    --stage-bg: #ffffff;
    --navy-deep: #070d1c;
    --navy: #0c1a3a;
    --bokeh-blue: #1d4f8f;
    --warm-red: #a3161b;
    --glitter-gold: #9c6a2a;
    --white: #ffffff;
    --gold-light: #fbeccd;
    --gold-mid: #e8c27e;
    --gold-deep: #c9954a;
  }
  * { box-sizing: border-box; margin: 0; padding: 0; }
  html, body {
    width: 1200px;
    height: 695px;
    overflow: hidden;
    background: var(--stage-bg);
  }
  .stage {
    position: relative;
    width: 1200px;
    height: 695px;
    display: flex;
    align-items: center;
    justify-content: center;
  }
  .cover {
    position: relative;
    width: 462px;
    height: 695px;
    overflow: hidden;
    background: var(--navy-deep);
    text-align: center;
    color: var(--white);
  }
  .cover-art {
    position: absolute;
    inset: 0;
    background:
      radial-gradient(ellipse 60% 22% at 15% 100%, rgba(156,106,42,0.75), transparent 75%),
      radial-gradient(ellipse 60% 22% at 90% 100%, rgba(156,106,42,0.75), transparent 75%),
      radial-gradient(ellipse 70% 45% at 100% 45%, rgba(29,79,143,0.85), transparent 75%),
      radial-gradient(ellipse 60% 45% at 0% 60%, rgba(29,79,143,0.55), transparent 75%),
      linear-gradient(180deg, var(--navy-deep) 0%, var(--navy) 35%, rgba(163,22,27,0.55) 65%, var(--navy-deep) 100%);
  }
  .cover-tagline {
    position: absolute;
    top: 26px;
    left: 0;
    right: 0;
    font-family: 'Montserrat', sans-serif;
    font-weight: 500;
    font-size: 12.4px;
    line-height: 15px;
    letter-spacing: 0.2px;
    text-transform: uppercase;
  }
  .book-title { font-weight: normal; }
  .title-lead {
    position: absolute;
    top: 216px;
    left: 0;
    right: 0;
    font-family: 'Bebas Neue', sans-serif;
    font-size: 96px;
    line-height: 1;
    letter-spacing: -1px;
  }
  .motion-streaks {
    position: absolute;
    top: 330px;
    left: 30px;
    width: 160px;
    height: 120px;
  }
  .title-script-wrap {
    position: absolute;
    top: 292px;
    left: 0;
    right: 0;
    perspective: 420px;
  }
  .title-script {
    display: inline-block;
    font-family: 'Kaushan Script', cursive;
    font-size: 150px;
    line-height: 1.2;
    padding: 0 24px;
    transform: rotateY(-32deg) rotateZ(-9deg) skewX(-8deg);
    transform-origin: 70% 50%;
    background: linear-gradient(100deg, var(--gold-light) 15%, var(--gold-mid) 55%, var(--gold-deep) 90%);
    -webkit-background-clip: text;
    background-clip: text;
    color: transparent;
  }
  .subtitle {
    position: absolute;
    top: 496px;
    left: 0;
    right: 0;
    font-family: 'Montserrat', sans-serif;
    font-weight: 800;
    font-size: 26px;
    line-height: 29px;
    text-transform: uppercase;
  }
  .author-first {
    position: absolute;
    top: 610px;
    left: 0;
    right: 0;
    font-family: 'Montserrat', sans-serif;
    font-weight: 800;
    font-size: 38px;
    line-height: 1;
    text-transform: uppercase;
    background: linear-gradient(90deg, var(--gold-deep), var(--gold-light) 50%, var(--gold-deep));
    -webkit-background-clip: text;
    background-clip: text;
    color: transparent;
  }
  .author-last {
    position: absolute;
    top: 649px;
    left: 0;
    right: 0;
    font-family: 'Montserrat', sans-serif;
    font-weight: 700;
    font-size: 17px;
    line-height: 1;
    letter-spacing: 6px;
    text-transform: uppercase;
  }
</style>
</head>
<body>
  <main class="stage">
    <section class="cover">
      <div class="cover-art" role="img" aria-label="Atmospheric background of deep navy with blue and gold bokeh light and a warm red glow"></div>
      <p class="cover-tagline">Lorem ipsum dolor sit amet, consectetur<br>adipiscing elit, sed do eiusmod tempor.</p>
      <h1 class="book-title">
        <span class="title-lead">STAY</span>
        <svg class="motion-streaks" viewBox="0 0 160 120" aria-hidden="true">
          <g stroke="#e8c27e" stroke-linecap="round" fill="none">
            <line x1="10" y1="78" x2="120" y2="58" stroke-width="3" opacity="0.85"/>
            <line x1="30" y1="96" x2="130" y2="78" stroke-width="2" opacity="0.6"/>
            <line x1="0" y1="60" x2="90" y2="44" stroke-width="1.5" opacity="0.45"/>
          </g>
        </svg>
        <span class="title-script-wrap"><span class="title-script">Bold</span></span>
      </h1>
      <p class="subtitle">Build On Lasting<br>Discipline</p>
      <p class="author-first">Margaret</p>
      <p class="author-last">Holloway</p>
    </section>
  </main>
</body>
</html>
```